Automotive component supplier needs a business card design

We need a business card design for our company called Velran Global Components Ltd based in the UK. We are a supplier of interior and exterior components to premium car manufacturers such as Corvel Ashby, Hadley Fenn, Marquist and Tavarelli. We would like to see a modern business card design that uses the colour blue.

Target Market(s)

Premium automotive car manufacturers.

Industry/Entity Type

Automotive

Contact Information for Business Card

Company Name : Velran Global Components Limited
Address: 17 Marlow Yard, Upper Heath, Warwick, CV31 8QL, United Kingdom
Web Address : www.velrancomponents-example.co.uk

Font styles to use
Other font styles liked:
• Helvetica

Colors
3176b5
0255a3
85acd3
cfdeed
cee9f5
85cae6
34a6d7
0692cd
9bcb3c

Requirements
Must have
• Clear company logo and a mixture of blue colours.
Nice to have
• A high quality modern image.
Should not have
• Multiple colours.

```html
<!DOCTYPE html>
<html lang="en">
<head>
<meta charset="utf-8">
<title>Velran Global Components – Business Card</title>
<link rel="stylesheet" href="https://fonts.googleapis.com/css2?family=Roboto+Condensed:wght@400;700&display=swap">
<style>
  :root {
    --stage: #2b2e33;
    --blue: #0692cd;
    --green: #9bcb3c;
    --white: #ffffff;
    --charcoal: #333436;
    --text-on-blue: #ffffff;
  }
  * { box-sizing: border-box; margin: 0; padding: 0; }
  html, body {
    width: 1200px; height: 900px; overflow: hidden;
    background: var(--stage);
    font-family: "Roboto Condensed", "Helvetica Neue", Arial, sans-serif;
  }
  .canvas {
    width: 1200px; height: 900px;
    display: flex; align-items: center; justify-content: center; gap: 40px;
  }
  .card {
    position: relative;
    width: 540px; height: 310px;
    border-radius: 22px;
    overflow: hidden;
    box-shadow: 0 14px 30px rgba(0,0,0,.45);
  }
  /* Front */
  .card-front { background: var(--white); }
  .card-front .shape { position: absolute; inset: 0; width: 100%; height: 100%; }
  .brand {
    position: absolute;
    display: flex; align-items: center; gap: 10px;
    font-weight: 700; white-space: nowrap;
  }
  .brand-mark { width: 16px; height: 16px; background: var(--green); flex: none; }
  .card-front .brand {
    left: 128px; top: 60px;
    font-size: 32px; color: var(--blue);
  }
  .person { position: absolute; left: 34px; top: 172px; color: var(--text-on-blue); }
  .person-name { font-weight: 700; font-size: 26px; line-height: 1; }
  .person-name .surname { color: var(--green); }
  .person-role { font-weight: 700; font-size: 13px; margin-top: 6px; letter-spacing: .3px; }
  .address {
    position: absolute; left: 34px; bottom: 20px;
    font-size: 11px; color: var(--text-on-blue); white-space: nowrap;
  }
  .contact {
    position: absolute; left: 290px; top: 186px;
    list-style: none; color: var(--text-on-blue); font-size: 12px;
  }
  .contact li { display: flex; align-items: center; gap: 8px; line-height: 20px; white-space: nowrap; }
  .contact svg { width: 12px; height: 12px; flex: none; }
  /* Back */
  .card-back { background: var(--charcoal); }
  .band-top { position: absolute; left: 0; right: 0; top: 0; height: 16px; background: var(--blue); }
  .band-top-line { position: absolute; left: 0; right: 0; top: 16px; height: 3px; background: var(--green); }
  .band-bottom { position: absolute; left: 0; right: 0; bottom: 0; height: 14px; display: flex; }
  .band-bottom .b { flex: 1; background: var(--blue); }
  .band-bottom .g { flex: 1; background: var(--green); }
  .card-back .brand {
    left: 50%; top: 50%; transform: translate(-50%, -50%);
    font-size: 38px; color: var(--white);
  }
</style>
</head>
<body>
<main class="canvas">
  <section class="card card-front" aria-label="Business card front">
    <svg class="shape" viewBox="0 0 540 310" preserveAspectRatio="none" aria-hidden="true">
      <path d="M0 0 H40 C30 60 40 120 110 140 C220 165 380 160 470 175 C525 185 540 250 522 310 H0 Z" fill="var(--blue)"/>
    </svg>
    <div class="brand"><span class="brand-mark"></span><span>Velran Global Components</span></div>
    <div class="person">
      <p class="person-name">Dorian <span class="surname">Kell</span></p>
      <p class="person-role">CEO/FOUNDER</p>
    </div>
    <ul class="contact">
      <li><svg viewBox="0 0 12 12"><path d="M2 1h3l1 3-2 1a7 7 0 0 0 3 3l1-2 3 1v3c0 1-1 1-1 1A10 10 0 0 1 1 2s0-1 1-1z" fill="var(--green)"/></svg>014-582-3067</li>
      <li><svg viewBox="0 0 12 12"><rect x="3" y="0.5" width="6" height="11" rx="1" fill="none" stroke="var(--green)" stroke-width="1.2"/></svg>014-582-3068</li>
      <li><svg viewBox="0 0 12 12"><rect x="0.5" y="2" width="11" height="8" fill="var(--green)"/><path d="M1 2.5l5 4 5-4" fill="none" stroke="var(--blue)" stroke-width="1"/></svg>dorian.kell@mailbox-example.com</li>
      <li><svg viewBox="0 0 12 12"><circle cx="6" cy="6" r="5.5" fill="var(--green)"/></svg>www.velrancomponents-example.co.uk</li>
    </ul>
    <p class="address">17 Marlow Yard, Upper Heath, Warwick, CV31 8QL, UK</p>
  </section>

  <section class="card card-back" aria-label="Business card back">
    <div class="band-top"></div>
    <div class="band-top-line"></div>
    <div class="brand"><span class="brand-mark"></span><span>Velran Global Components</span></div>
    <div class="band-bottom"><span class="b"></span><span class="g"></span></div>
  </section>
</main>
</body>
</html>
```